Business Cards for a law firm

Business cards for our law firm. Use our silhoette logo and OAK PARTNERS - check our website (www.oakpartners.example)

Contact Information for Business Card

our silhouette logo, OAK PARTNERS, 800-555-0147, Dorian Pemberton, dorian@oakpartners.example

Requirements
Must have
• our silhouette logo, OAK PARTNERS, 800-555-0147, Dorian Pemberton, dorian@oakpartners.example

```html
<!DOCTYPE html>
<html lang="en">
<head>
<meta charset="utf-8">
<title>Oak Partners – Business Cards</title>
<link rel="stylesheet" href="https://fonts.googleapis.com/css2?family=Marcellus+SC&family=Montserrat:wght@300;400;700&display=swap">
<style>
  :root {
    --backdrop: #8a8a88;
    --card-white: #ffffff;
    --navy: #27347a;
    --navy-deep: #1e2a63;
    --navy-light: #5a6fb8;
    --text-grey: #6e6e74;
    --rule: #3b4785;
  }
  * { margin: 0; padding: 0; box-sizing: border-box; }
  html, body { width: 1200px; height: 791px; overflow: hidden; }
  body {
    background: var(--backdrop);
    font-family: "Montserrat", Arial, sans-serif;
    position: relative;
  }
  .card {
    position: absolute;
    left: 320px;
    width: 560px;
    height: 320px;
    box-shadow: 0 6px 18px rgba(0,0,0,0.25);
  }
  .card--front { top: 60px; background: var(--card-white); border-bottom: 3px solid var(--navy); }
  .card--back { top: 411px; background: var(--navy); overflow: hidden; }

  .brand {
    display: flex;
    align-items: center;
    gap: 12px;
    font-family: "Marcellus SC", Georgia, serif;
    letter-spacing: 0.12em;
    font-size: 25px;
    white-space: nowrap;
  }
  .brand__mark { width: 22px; height: 22px; flex: none; }
  .brand--navy { color: var(--navy); }
  .brand--navy .brand__mark { background: var(--navy); }
  .brand--white { color: #ffffff; }
  .brand--white .brand__mark { background: #ffffff; }

  .card--front .brand { position: absolute; left: 34px; top: 146px; }
  .divider {
    position: absolute;
    left: 282px; top: 108px;
    width: 1.5px; height: 104px;
    background: var(--rule);
  }
  .contact { position: absolute; left: 306px; top: 110px; }
  .contact__name {
    font-weight: 700;
    color: var(--navy);
    font-size: 19px;
    letter-spacing: 0.01em;
    margin-bottom: 12px;
    white-space: nowrap;
  }
  .contact__list { list-style: none; }
  .contact__item {
    display: flex; align-items: center; gap: 9px;
    color: var(--text-grey);
    font-weight: 300;
    font-size: 14px;
    line-height: 24px;
    white-space: nowrap;
  }
  .contact__icon { width: 12px; height: 12px; flex: none; }

  .pattern-field {
    position: absolute; inset: 0;
    background: linear-gradient(110deg, var(--navy-deep) 0%, var(--navy) 45%, var(--navy-light) 100%);
    opacity: 0.9;
  }
  .card--back .brand { position: absolute; right: 52px; top: 150px; font-size: 27px; }
</style>
</head>
<body>
  <section class="card card--front" aria-label="Business card front">
    <div class="brand brand--navy"><span class="brand__mark"></span>OAK PARTNERS</div>
    <div class="divider"></div>
    <div class="contact">
      <p class="contact__name">DORIAN PEMBERTON</p>
      <ul class="contact__list">
        <li class="contact__item">
          <svg class="contact__icon" viewBox="0 0 12 12" aria-hidden="true"><path d="M2.5 1 L4.5 1 L5.3 3.6 L4 4.6 Q5 7 7.4 8 L8.4 6.7 L11 7.5 L11 9.5 Q10.5 11 9 11 Q1 10 1 3 Q1 1.5 2.5 1 Z" fill="var(--navy)"/></svg>
          800-555-0147
        </li>
        <li class="contact__item">
          <svg class="contact__icon" viewBox="0 0 12 12" aria-hidden="true"><rect x="0.5" y="2.5" width="11" height="7.5" fill="var(--navy)"/><path d="M0.8 2.8 L6 6.8 L11.2 2.8" stroke="#fff" stroke-width="1" fill="none"/></svg>
          dorian@oakpartners.example
        </li>
        <li class="contact__item">
          <svg class="contact__icon" viewBox="0 0 12 12" aria-hidden="true"><circle cx="6" cy="6" r="5.5" fill="var(--navy)"/><path d="M0.5 6 H11.5 M6 0.5 Q3 6 6 11.5 M6 0.5 Q9 6 6 11.5" stroke="#fff" stroke-width="0.8" fill="none"/></svg>
          www.oakpartners.example
        </li>
      </ul>
    </div>
  </section>

  <section class="card card--back" aria-label="Business card back">
    <div class="pattern-field" role="img" aria-label="Repeating pattern of the firm's silhouette emblem in shades of blue"></div>
    <div class="brand brand--white"><span class="brand__mark"></span>OAK PARTNERS</div>
  </section>
</body>
</html>
```